Jolly Dabbers - Face Painting Company requires business card design

Hi,
I am wanting a business card design for a new business in Brisbane (Australia) called 'Jolly Dabbers'. We are a childrens face painting company.

I want to communicate a corporate, simple and clean message through my business card, but also fun and relevant to children.

My company colours are black, yellow and purple, and at the moment I am running with a "cheeky smile" type theme, along the lines of the Fenwick Fox (Tobias and the Glasshouse).

I want this to look Corporate, clean and simple. On the back I would like to see some creative flair with a border or background design, perhaps in white or another colour.

• Front:
Jolly Dabbers
Face Painting Designs

Back:
Maren Ellwick
Artist
0491 283 046
maren@jollydabbers.com.au
www.jollydabbers.com.au
• Attached is the banner which i had made, the business card should go along with this type of theme.
I would like to use the colours Yellow, Black and Purple. Purple should be used in a miniml way, with yellow and black as the main colours.
I want it to have a CORPORATE look.

A Playfull but readable text.

I would like a mix up of the colours on the back in the text.
Maren Ellwick (black)
Artist(purple) etc.

```html
<!DOCTYPE html>
<html lang="en">
<head>
<meta charset="utf-8">
<title>Jolly Dabbers – Business Card</title>
<link rel="stylesheet" href="https://fonts.googleapis.com/css2?family=Bangers&family=Open+Sans:wght@800&family=Jost:wght@500&family=Arimo&display=swap">
<style>
  :root {
    --backdrop: #ece9e2;
    --card-yellow: #f3ee56;
    --card-white: #ffffff;
    --ink-black: #141414;
    --brand-purple: #76439a;
    --swirl-white: rgba(255, 255, 255, 0.85);
  }
  * { margin: 0; padding: 0; box-sizing: border-box; }
  html, body {
    width: 1200px;
    height: 800px;
    overflow: hidden;
    background: var(--backdrop);
  }
  .stage {
    position: relative;
    width: 1200px;
    height: 800px;
  }
  .card {
    position: absolute;
    width: 552px;
    height: 336px;
    overflow: hidden;
  }
  /* Front */
  .card-front {
    left: 103px;
    top: 52px;
    background: var(--card-yellow);
  }
  .swirl-decoration {
    position: absolute;
    right: 0;
    top: 0;
    width: 410px;
    height: 336px;
    background: radial-gradient(ellipse at 78% 55%, var(--swirl-white) 0%, rgba(255,255,255,0.35) 40%, rgba(255,255,255,0) 72%);
  }
  .brand-name {
    position: absolute;
    left: 28px;
    top: 112px;
    font-family: "Bangers", "Comic Sans MS", cursive;
    font-size: 52px;
    letter-spacing: 2px;
    line-height: 1;
    color: var(--ink-black);
  }
  .brand-tagline {
    position: absolute;
    left: 72px;
    top: 172px;
    font-family: "Open Sans", Arial, sans-serif;
    font-weight: 800;
    font-size: 25px;
    letter-spacing: 1.2px;
    line-height: 1;
    color: var(--brand-purple);
  }
  /* Back */
  .card-back {
    left: 544px;
    top: 413px;
    background: var(--card-white);
  }
  .artist-name {
    position: absolute;
    left: 30px;
    top: 128px;
    font-family: "Jost", "Futura", sans-serif;
    font-weight: 500;
    font-size: 35px;
    line-height: 1;
    color: var(--ink-black);
  }
  .artist-role {
    position: absolute;
    left: 30px;
    top: 168px;
    font-family: "Bangers", "Comic Sans MS", cursive;
    font-size: 38px;
    letter-spacing: 3px;
    line-height: 1;
    color: var(--brand-purple);
  }
  .contact-band {
    position: absolute;
    left: 324px;
    top: 131px;
    width: 228px;
    height: 70px;
    padding: 7px 0 0 9px;
    background: var(--card-yellow);
    font-family: "Arimo", Arial, sans-serif;
    color: var(--ink-black);
    list-style: none;
  }
  .contact-band li {
    font-size: 13px;
    line-height: 17px;
  }
  .contact-band .contact-phone {
    font-size: 15px;
  }
</style>
</head>
<body>
<main class="stage">
  <section class="card card-front" aria-label="Business card front">
    <div class="swirl-decoration" role="img" aria-label="Flowing white swirl ornament"></div>
    <h1 class="brand-name">JOLLY DABBERS</h1>
    <p class="brand-tagline">FACE PAINTING DESIGNS</p>
  </section>

  <section class="card card-back" aria-label="Business card back">
    <h2 class="artist-name">Maren Ellwick</h2>
    <p class="artist-role">ARTIST</p>
    <ul class="contact-band">
      <li class="contact-phone">0491 283 046</li>
      <li class="contact-email">maren@jollydabbers.com.au</li>
      <li class="contact-web">www.jollydabbers.com.au</li>
    </ul>
  </section>
</main>
</body>
</html>
```